VORTEQ

It’s is a startup business. We design and build new products.

Target Market(s)

For my first two products, they are targeting the laundry market, hanger accessory, and new modern style clothes dryer. I also have a Pet Treat product at patent stage, and there are other products not yet started but will be more engineering based. Therefore from young adults to older population

Industry/Entity Type

Colours of website to match the logo (att)

Coding

Coded - Design and coding required

Number of Pages Required

1 page

Font styles to use
Other font styles liked:
• Some of the same font as the logo

Colors

Designer to choose colors to be used in the design.

Requirements
Must have
• An upbeat vibe - the logo looks great so inline with that !
Should not have
• anything old fashioned and old style fonts

```html
<!DOCTYPE html>
<html lang="en">
<head>
<meta charset="UTF-8">
<title>VORTEQ – Innovative Designs for a Modern World</title>
<link rel="stylesheet" href="https://fonts.googleapis.com/css2?family=Montserrat:ital,wght@0,400;0,500;0,600;1,400&family=Orbitron:wght@500;600&display=swap">
<style>
:root{
  --teal:#00c9cc;
  --teal-dark:#0a9fb0;
  --navy:#1b2a6b;
  --navy-deep:#0f1546;
  --purple:#4a1a5c;
  --magenta:#c44fd0;
  --page:#ebe9ea;
  --white:#ffffff;
  --ink:#1a1a1a;
  --muted:#777;
  --nav:#3a3a3a;
  --head-blue:#2a3a8a;
}
*{margin:0;padding:0;box-sizing:border-box}
html,body{width:1200px;height:3535px;overflow:hidden}
body{background:var(--page);font-family:'Montserrat',sans-serif;color:var(--ink)}
.page{position:relative;width:1200px;height:3535px;overflow:hidden}
.abs{position:absolute}

/* header */
.site-header{position:absolute;left:0;top:0;width:1200px;height:85px;background:var(--white);z-index:3}
.brand{position:absolute;left:111px;top:26px;display:flex;align-items:center;gap:10px;font-weight:600;font-size:26px;letter-spacing:4px;color:var(--navy)}
.brand-dot{width:22px;height:22px;border-radius:50%;background:var(--teal)}
.main-nav a{position:absolute;top:33px;font-size:15px;color:var(--nav);text-decoration:none}
.main-nav a.active{color:var(--head-blue);font-weight:600}
.search-icon{position:absolute;left:1127px;top:34px}

/* hero */
.hero{position:absolute;left:0;top:85px;width:1200px;height:520px}
.hero-title{position:absolute;left:111px;top:152px;font-family:'Orbitron',sans-serif;font-weight:600;font-size:31px;line-height:38px;letter-spacing:2px;color:var(--white);text-transform:uppercase}
.hero-text{position:absolute;left:111px;top:246px;width:520px;font-size:15.5px;line-height:26px;color:var(--white)}
.btn{position:absolute;display:flex;align-items:center;justify-content:center;background:var(--teal);color:var(--navy-deep);font-size:15px;text-decoration:none;height:37px}

/* section headings */
.section-title{position:absolute;display:flex;align-items:center;gap:14px;font-family:'Orbitron',sans-serif;font-weight:500;font-size:30px;letter-spacing:3px;text-transform:uppercase;color:var(--navy)}
.section-title .mark{width:40px;height:40px;border-radius:50%;background:linear-gradient(135deg,var(--teal),var(--navy))}
.section-title.light{color:var(--white)}

/* about */
.about-lead{position:absolute;left:600px;top:776px;width:470px;font-size:17.5px;line-height:26px;font-weight:500}
.about-body{position:absolute;left:600px;top:843px;width:490px;font-size:14.6px;line-height:25.7px;color:#7a7a7a}

/* industries */
.industries{position:absolute;left:0;top:1218px;width:1200px;height:720px;background:linear-gradient(180deg,#0aa8b8 0%,#1a70a4 45%,#243d8a 100%);overflow:hidden}
.industry-card{position:absolute;top:199px;width:466px;height:432px;background:var(--white);border-radius:16px}
.industry-photo{position:absolute;left:28px;top:28px;width:410px;height:272px;border-radius:16px}
.industry-card h3{position:absolute;left:0;top:333px;width:100%;text-align:center;font-size:21px;font-weight:600}
.industry-card p{position:absolute;left:0;top:363px;width:100%;text-align:center;font-size:12.5px;line-height:21px;color:#666}
.slider-arrow{position:absolute;top:388px;width:56px;height:56px;border-radius:50%;background:var(--white);display:flex;align-items:center;justify-content:center}

/* technology */
.tech-item{position:absolute;top:2142px;width:240px;text-align:center}
.tech-icon{width:128px;height:128px;margin:0 auto;border-radius:50%;background:radial-gradient(circle at 40% 35%,#2a8ec4,#1b4c92 70%);border:3px solid #173a78;display:flex;align-items:center;justify-content:center}
.tech-item span{display:block;margin-top:22px;font-size:18px;font-weight:500}
.tech-divider{position:absolute;top:2173px;width:2px;height:108px;background:#8a8a8a}
.rule{position:absolute;left:111px;top:2403px;width:978px;height:1px;background:#8a8a8a}

/* blog */
.blog-intro{position:absolute;left:114px;top:2580px;width:660px;font-size:17.5px;line-height:26px;font-weight:500}
.post{position:absolute;top:2675px;width:305px}
.post-photo{width:305px;height:206px}
.post time{display:block;margin-top:23px;font-style:italic;font-size:14px;color:var(--head-blue)}
.post h3{margin-top:10px;font-size:17.5px;line-height:26px;font-weight:500}
.post p{margin-top:20px;font-size:13.8px;line-height:23px;color:#7a7a7a}

/* footer */
.site-footer{position:absolute;left:0;top:3160px;width:1200px;height:375px}
.footer-brand{position:absolute;left:0;top:178px;width:1200px;display:flex;justify-content:center;align-items:center;gap:18px;font-size:50px;font-weight:600;letter-spacing:8px;color:var(--white)}
.footer-brand .brand-dot{width:40px;height:40px}
.footer-nav a{position:absolute;top:274px;transform:translateX(-50%);font-size:19px;color:var(--white);text-decoration:none}
.footer-rule{position:absolute;left:111px;top:324px;width:978px;height:1px;background:rgba(255,255,255,.6)}
.copyright{position:absolute;left:0;top:336px;width:1200px;text-align:center;font-size:12.5px;color:#d8dbf0}
</style>
</head>
<body>
<div class="page">

  <header class="site-header">
    <div class="brand"><span class="brand-dot"></span>VORTEQ</div>
    <nav class="main-nav">
      <a class="active" href="#" style="left:448px">Home</a>
      <a href="#" style="left:543px">About Us</a>
      <a href="#" style="left:661px">Products</a>
      <a href="#" style="left:777px">Technology</a>
      <a href="#" style="left:914px">Blog</a>
      <a href="#" style="left:995px">Contact Us</a>
    </nav>
    <svg class="search-icon" width="15" height="15" viewBox="0 0 15 15"><circle cx="6" cy="6" r="4.5" fill="none" stroke="#333" stroke-width="2"/><line x1="9.5" y1="9.5" x2="14" y2="14" stroke="#333" stroke-width="2"/></svg>
  </header>

  <section class="hero">
    <svg class="abs" style="left:0;top:0" width="1200" height="520" viewBox="0 0 1200 520">
      <defs>
        <linearGradient id="heroBg" x1="0" y1="0" x2="1" y2="0">
          <stop offset="0" stop-color="#35123f"/>
          <stop offset=".55" stop-color="#5a1f6e"/>
          <stop offset="1" stop-color="#7a2c8a"/>
        </linearGradient>
        <radialGradient id="heroGlow" cx="0.72" cy="0.42" r="0.35">
          <stop offset="0" stop-color="#e07be6" stop-opacity=".9"/>
          <stop offset="1" stop-color="#e07be6" stop-opacity="0"/>
        </radialGradient>
      </defs>
      <path d="M0 0H1200V455C1100 410 960 420 760 465C520 520 260 560 0 455Z" fill="url(#heroBg)"/>
      <rect role="img" aria-label="Glowing network of connected points floating above an open hand" x="560" y="0" width="640" height="430" fill="url(#heroGlow)"/>
    </svg>
    <h1 class="hero-title">Innovative Designs<br>for a Modern</h1>
    <p class="hero-text">Lorem ipsum dolor sit amet, consectetur adipiscing elit, sed do eiusmod tempor incididunt ut labore</p>
    <a class="btn" href="#" style="left:111px;top:320px;width:168px">Get Started</a>
  </section>

  <section class="about">
    <svg class="abs" style="left:111px;top:715px" width="430" height="390" viewBox="0 0 430 390">
      <defs>
        <linearGradient id="crescent" x1="0" y1="0" x2="0" y2="1">
          <stop offset="0" stop-color="#0aa3b8"/><stop offset="1" stop-color="#1b3f86"/>
        </linearGradient>
        <linearGradient id="aboutPhoto" x1="0" y1="0" x2="1" y2="1">
          <stop offset="0" stop-color="#1d3c66"/><stop offset="1" stop-color="#0d1a30"/>
        </linearGradient>
      </defs>
      <path d="M300 30C380 90 420 210 360 300C330 345 290 370 245 380C330 330 370 230 340 140C330 100 310 60 300 30Z" fill="url(#crescent)"/>
      <circle role="img" aria-label="Businesswoman holding a tablet in a server room" cx="194" cy="194" r="194" fill="url(#aboutPhoto)"/>
    </svg>
    <h2 class="section-title" style="left:600px;top:698px"><span class="mark"></span>About Us</h2>
    <p class="about-lead">Lorem ipsum dolor sit amet, consectetur adipiscing elit, sed do eiusmod tempor</p>
    <p class="about-body">Sed ut perspiciatis unde omnis iste natus error sit voluptatem accusantium doloremque laudantium, totam rem aperiam, eaque ipsa quae ab illo inventore veritatis et quasi architecto beatae vitae dicta sunt explicabo. Nemo enim ipsam voluptatem quia voluptas sit aspernatur aut odit aut fugit, sed quia consequuntur magni dolores eos qui ratione voluptatem sequi nesciunt. Neque porro quisquam est, qui dolorem ipsum quia dolor sit amet, consectetur, adipisci velit, sed quia non numquam eius modi tempora incidunt ut labore et dolore magnam aliquam quaerat voluptatem.</p>
    <a class="btn" href="#" style="left:600px;top:1094px;width:144px">Read More</a>
  </section>

  <section class="industries">
    <svg class="abs" style="left:0;top:0" width="1200" height="720" viewBox="0 0 1200 720" aria-hidden="true">
      <circle cx="686" cy="85" r="65" fill="#ffffff" fill-opacity=".08"/>
      <circle cx="108" cy="676" r="28" fill="#3a62b4" fill-opacity=".6"/>
      <circle cx="1162" cy="571" r="17" fill="#1a9ad0" fill-opacity=".6"/>
      <circle cx="520" cy="720" r="130" fill="#3a4ba0" fill-opacity=".5"/>
    </svg>
    <h2 class="section-title light" style="left:333px;top:101px"><span class="mark"></span>Our Industries</h2>
    <article class="industry-card" style="left:111px">
      <div class="industry-photo" role="img" aria-label="Shopper reading her phone while holding a bottle of laundry detergent" style="background:linear-gradient(135deg,#c9b9a8,#a58a6c 60%,#7fc7d3)"></div>
      <h3>Laundry Market</h3>
      <p>Lorem ipsum dolor sit amet,<br>consectetur adipiscing elit, sed do eiusmod tempor incididunt</p>
    </article>
    <article class="industry-card" style="left:622px">
      <div class="industry-photo" role="img" aria-label="Woman holding a small dog in a pet store aisle" style="background:linear-gradient(135deg,#6a5fb0,#d8d2cc 55%,#8a7a6a)"></div>
      <h3>Pet Treat</h3>
      <p>Lorem ipsum dolor sit amet,<br>consectetur adipiscing elit, sed do eiusmod tempor incididunt</p>
    </article>
    <div class="slider-arrow" style="left:34px"><svg width="16" height="24" viewBox="0 0 16 24"><path d="M12 3L4 12L12 21" fill="none" stroke="#1b2a6b" stroke-width="3"/></svg></div>
    <div class="slider-arrow" style="left:1109px"><svg width="16" height="24" viewBox="0 0 16 24"><path d="M4 3L12 12L4 21" fill="none" stroke="#1b2a6b" stroke-width="3"/></svg></div>
  </section>

  <section class="technology">
    <h2 class="section-title" style="left:298px;top:2037px"><span class="mark"></span>Our Technology</h2>
    <div class="tech-item" style="left:71px">
      <div class="tech-icon"><svg width="50" height="56" viewBox="0 0 50 56" fill="none" stroke="#fff" stroke-width="2.5"><path d="M25 4C13 4 6 13 6 22c0 8 6 12 9 18v6h20v-6c3-6 9-10 9-18C44 13 37 4 25 4Z"/><line x1="17" y1="51" x2="33" y2="51"/><path d="M25 12v26M18 20c4 0 7 3 7 6M32 20c-4 0-7 3-7 6"/></svg></div>
      <span>Smart Technology</span>
    </div>
    <div class="tech-divider" style="left:303px"></div>
    <div class="tech-item" style="left:319px">
      <div class="tech-icon"><svg width="60" height="56" viewBox="0 0 60 56" fill="none" stroke="#fff" stroke-width="2.5"><path d="M8 26a22 22 0 0 0 44 0Z"/><path d="M18 26V12h6v14M28 26V6h6v20M38 26V16h5v10"/><circle cx="30" cy="52" r="3"/><circle cx="6" cy="42" r="3"/><circle cx="54" cy="42" r="3"/></svg></div>
      <span>Sustainable Technology</span>
    </div>
    <div class="tech-divider" style="left:578px"></div>
    <div class="tech-item" style="left:601px">
      <div class="tech-icon"><svg width="60" height="50" viewBox="0 0 60 50" fill="none" stroke="#fff" stroke-width="2.5"><path d="M4 44h52"/><path d="M10 44V30l8-14 8 6M50 44V30l-8-14-8 6"/><circle cx="30" cy="36" r="6"/></svg></div>
      <span>Advanced Manufacturing</span>
    </div>
    <div class="tech-divider" style="left:865px"></div>
    <div class="tech-item" style="left:864px">
      <div class="tech-icon"><svg width="56" height="56" viewBox="0 0 56 56" fill="none" stroke="#fff" stroke-width="2.5"><path d="M22 6l16 6v14c0 12-8 20-16 24C14 46 6 38 6 26V12Z"/><path d="M14 28l6 6 10-12"/><circle cx="46" cy="16" r="4"/><circle cx="48" cy="34" r="4"/><path d="M38 20l5-2M38 32l6 1"/></svg></div>
      <span style="margin-top:24px">Advanced Materials</span>
    </div>
  </section>

  <div class="rule"></div>

  <section class="blog">
    <h2 class="section-title" style="left:114px;top:2503px"><span class="mark"></span>Latest Blog</h2>
    <p class="blog-intro">Lorem ipsum dolor sit amet, consectetur adipiscing elit, sed do eiusmod tempor incididunt ut labore et dolore magna aliqua.</p>
    <a class="btn" href="#" style="left:946px;top:2591px;width:144px">View More</a>
    <article class="post" style="left:114px">
      <div class="post-photo" role="img" aria-label="Two colleagues reviewing work on a tablet in an office" style="background:linear-gradient(135deg,#3f6c9c,#b9c9da 60%,#3b4f73)"></div>
      <time>May 19, 2023</time>
      <h3>Lorem ipsum dolor sit amet, con adipiscing elit,</h3>
      <p>Sed ut perspiciatis unde omnis iste natus error sit voluptatem accusantium dolore mque laudantium, totam rem aperiam, eaque ipsa quae ab .....</p>
    </article>
    <article class="post" style="left:449px">
      <div class="post-photo" role="img" aria-label="Hands typing on a laptop keyboard with glowing digital icons" style="background:linear-gradient(135deg,#1a2a3a,#2c5a7a 55%,#d9853a)"></div>
      <time>May 19, 2023</time>
      <h3>Lorem ipsum dolor sit amet, con adipiscing elit,</h3>
      <p>Sed ut perspiciatis unde omnis iste natus error sit voluptatem accusantium dolore mque laudantium, totam rem aperiam, eaque ipsa quae ab .....</p>
    </article>
    <article class="post" style="left:784px">
      <div class="post-photo" role="img" aria-label="Woman wearing a virtual reality headset beside a laptop" style="background:linear-gradient(135deg,#5a6878,#c5ccd4 55%,#2a3040)"></div>
      <time>May 19, 2023</time>
      <h3>Lorem ipsum dolor sit amet, con adipiscing elit,</h3>
      <p>Sed ut perspiciatis unde omnis iste natus error sit voluptatem accusantium dolore mque laudantium, totam rem aperiam, eaque ipsa quae ab .....</p>
    </article>
  </section>

  <footer class="site-footer">
    <svg class="abs" style="left:0;top:0" width="1200" height="375" viewBox="0 0 1200 375">
      <defs>
        <linearGradient id="footBg" x1="0" y1="0" x2="0" y2="1">
          <stop offset="0" stop-color="#1e2a78"/><stop offset="1" stop-color="#0c1040"/>
        </linearGradient>
      </defs>
      <path d="M0 90C150 40 300 70 520 60C760 50 900 0 1070 20C1130 28 1170 50 1200 70V375H0Z" fill="url(#footBg)"/>
    </svg>
    <div class="footer-brand"><span class="brand-dot"></span>VORTEQ</div>
    <nav class="footer-nav">
      <a href="#" style="left:242px">Home</a>
      <a href="#" style="left:371px">About Us</a>
      <a href="#" style="left:515px">Products</a>
      <a href="#" style="left:669px">Technology</a>
      <a href="#" style="left:802px">Blog</a>
      <a href="#" style="left:934px">Contact Us</a>
    </nav>
    <div class="footer-rule"></div>
    <p class="copyright">Copyright © 2025 Vorteq Innovation &amp; Technical Services. All rights reserved.</p>
  </footer>

</div>
</body>
</html>
```